Business Cards for a law firm

Business cards for our law firm. Use our silhoette logo and OAK PARTNERS - check our website (www.oakpartners.example)

Contact Information for Business Card

our silhouette logo, OAK PARTNERS, 800-555-0147, Dorian Pemberton, dorian@oakpartners.example

Requirements
Must have
• our silhouette logo, OAK PARTNERS, 800-555-0147, Dorian Pemberton, dorian@oakpartners.example

```html
<!DOCTYPE html>
<html lang="en">
<head>
<meta charset="utf-8">
<title>Oak Partners — Business Card</title>
<link rel="stylesheet" href="https://fonts.googleapis.com/css2?family=Montserrat:wght@400;700&display=swap">
<style>
  :root {
    --page-bg: #e3e7e9;
    --card-bg: #f0f0f1;
    --navy: #24326e;
    --pattern-light: #f7f7f8;
    --pattern-dark: #d9d9db;
  }
  * { margin: 0; padding: 0; box-sizing: border-box; }
  html, body {
    width: 1200px; height: 960px; overflow: hidden;
    background: var(--page-bg);
    font-family: "Montserrat", sans-serif;
    color: var(--navy);
  }
  .canvas { position: relative; width: 1200px; height: 960px; }

  .card {
    position: absolute; top: 105px;
    width: 428px; height: 750px;
    border-radius: 28px;
    background: var(--card-bg);
    border-left: 4px solid var(--navy);
    border-bottom: 4px solid var(--navy);
    overflow: hidden;
  }
  .card--front { left: 144px; }
  .card--back  { left: 631px; }

  .front-pattern {
    position: absolute; inset: 0;
    background: linear-gradient(100deg, var(--pattern-light) 0%, #ececee 45%, var(--pattern-dark) 100%);
  }
  .front-mark {
    position: absolute; left: 201px; top: 335px;
    transform: translate(-50%, -50%) rotate(-90deg);
    display: flex; align-items: center; gap: 18px;
    white-space: nowrap;
  }
  .front-mark__square {
    width: 34px; height: 34px; background: var(--navy);
  }
  .front-mark__name {
    font-size: 44px; font-weight: 400; letter-spacing: 1px; line-height: 1;
  }

  .back-mark {
    position: absolute; left: 91px; top: 42px;
    display: flex; align-items: center; gap: 14px;
  }
  .back-mark__square { width: 44px; height: 44px; background: var(--navy); }
  .back-mark__name {
    font-size: 27px; font-weight: 400; line-height: 0.95; letter-spacing: 0.5px;
  }

  .holder-name {
    position: absolute; left: 0; right: 0; top: 531px;
    text-align: center; font-size: 28px; letter-spacing: 0.5px; font-weight: 400;
    white-space: nowrap;
  }
  .holder-name strong { font-weight: 700; }

  .contact-icons {
    position: absolute; left: 0; right: 0; top: 576px;
    display: flex; justify-content: center; align-items: center; gap: 8px;
  }
  .contact-icons__rule { width: 56px; height: 2px; background: var(--navy); margin: 0 2px; }
  .contact-icons svg { width: 32px; height: 32px; display: block; }

  .contact-lines {
    position: absolute; left: 0; right: 0; top: 619px;
    text-align: center; line-height: 24px; letter-spacing: 1px;
  }
  .contact-lines .phone { font-size: 20px; line-height: 26px; }
  .contact-lines .web, .contact-lines .email { font-size: 15px; text-transform: uppercase; }
</style>
</head>
<body>
<div class="canvas">

  <section class="card card--front">
    <div class="front-pattern" role="img" aria-label="Faint repeating firm emblem pattern across the card face"></div>
    <div class="front-mark">
      <span class="front-mark__square"></span>
      <span class="front-mark__name">OAK PARTNERS</span>
    </div>
  </section>

  <section class="card card--back">
    <div class="back-mark">
      <span class="back-mark__square"></span>
      <span class="back-mark__name">OAK<br>PARTNERS</span>
    </div>

    <h1 class="holder-name"><strong>DORIAN</strong> PEMBERTON</h1>

    <div class="contact-icons">
      <span class="contact-icons__rule"></span>
      <svg viewBox="0 0 32 32" aria-label="Phone">
        <rect x="6" y="6" width="20" height="20" rx="3" transform="rotate(45 16 16)" fill="var(--navy)"/>
        <path d="M12.5 11.5c.6-.6 1.3-.4 1.7.2l.9 1.4c.3.5.2 1-.2 1.4l-.6.6c.6 1.3 1.5 2.2 2.8 2.8l.6-.6c.4-.4.9-.5 1.4-.2l1.4.9c.6.4.8 1.1.2 1.7l-.7.7c-.7.7-1.8.8-2.8.3-2.3-1.1-4.1-2.9-5.2-5.2-.5-1-.4-2.1.3-2.8z" fill="#fff"/>
      </svg>
      <svg viewBox="0 0 32 32" aria-label="Email">
        <rect x="6" y="6" width="20" height="20" rx="3" transform="rotate(45 16 16)" fill="var(--navy)"/>
        <rect x="10.5" y="12" width="11" height="8" fill="none" stroke="#fff" stroke-width="1.3"/>
        <path d="M10.5 12l5.5 4.5 5.5-4.5" fill="none" stroke="#fff" stroke-width="1.3"/>
      </svg>
      <svg viewBox="0 0 32 32" aria-label="Website">
        <rect x="6" y="6" width="20" height="20" rx="3" transform="rotate(45 16 16)" fill="var(--navy)"/>
        <circle cx="16" cy="16" r="5.5" fill="none" stroke="#fff" stroke-width="1.3"/>
        <ellipse cx="16" cy="16" rx="2.3" ry="5.5" fill="none" stroke="#fff" stroke-width="1"/>
        <path d="M10.5 16h11" stroke="#fff" stroke-width="1"/>
      </svg>
      <span class="contact-icons__rule"></span>
    </div>

    <div class="contact-lines">
      <p class="phone">800-555-0147</p>
      <p class="web">www.oakpartners.example</p>
      <p class="email">dorian@oakpartners.example</p>
    </div>
  </section>

</div>
</body>
</html>
```